4747 5858

Web(re)design of an existing directory search site www.le5858.be (in Dutch www.de4747.be and in English www.3838.be).

This site is a directory site, i.e. a "white pages" site whereby people can search the phone & details of another person based on a combination of name + city (for instance smith in Brussels); one can also search a company also based on a combination of name + city (for instance Vornak in Brussels); last but not least one can also search the name of the subscriber behind a specific telephone number (also called reverse search).

This site is quite outdated and needs a redesign, see instructions.

We need the output in XD format.

```html
<!DOCTYPE html>
<html lang="en">
<head>
<meta charset="utf-8">
<title>58 58 – Individuals search</title>
<link href="https://fonts.googleapis.com/css2?family=Poppins:wght@400;500;600&display=swap" rel="stylesheet">
<style>
  :root {
    --red: #d21c22;
    --dark: #3d3d3d;
    --paper: #f7f7f7;
    --white: #ffffff;
    --ink: #333333;
    --muted: #666666;
    --footer-link: #8a8a8a;
    --placeholder: #a9b4c8;
    --border: #e6e6e6;
  }
  * { box-sizing: border-box; margin: 0; padding: 0; }
  html, body { width: 1200px; height: 710px; overflow: hidden; }
  body { font-family: "Poppins", sans-serif; background: var(--white); position: relative; color: var(--ink); }

  .topbar { position: absolute; left: 0; top: 0; width: 1200px; height: 40px; background: var(--white); }
  .topbar__info { position: absolute; right: 165px; top: 11px; font-size: 13px; color: var(--ink); }
  .topbar__lang { position: absolute; right: 87px; top: 10px; display: flex; align-items: center; gap: 6px; font-size: 13px; }

  .navbar { position: absolute; left: 0; top: 40px; width: 1200px; height: 85px; background: var(--dark); border-bottom: 3px solid var(--red); }
  .brand { position: absolute; left: 88px; top: -30px; width: 120px; height: 100px; display: flex; align-items: center; gap: 6px; z-index: 2; }
  .brand__dot { width: 22px; height: 22px; border-radius: 50%; background: var(--red); flex: none; }
  .brand__name { font-size: 34px; font-weight: 600; color: var(--red); letter-spacing: 1px; line-height: 1; }
  .nav { position: absolute; left: 394px; top: 0; display: flex; height: 85px; }
  .nav__item { color: var(--white); font-size: 15px; font-weight: 500; padding: 0 18px; line-height: 85px; text-decoration: none; }
  .nav__item--active { background: var(--red); padding: 0 15px; }
  .nav__item + .nav__item { margin-left: 1px; }
  .quote { position: absolute; left: 962px; top: 22px; width: 150px; height: 42px; border: 1px solid var(--red); border-radius: 21px; padding: 3px; }
  .quote__btn { display: block; width: 100%; height: 100%; background: var(--red); border-radius: 18px; color: var(--white); font-size: 16px; font-weight: 600; text-align: center; line-height: 34px; }

  .search { position: absolute; left: 0; top: 128px; width: 600px; height: 542px; background: var(--paper); }
  .field { position: absolute; left: 184px; width: 305px; }
  .field__label { display: block; color: var(--red); font-size: 13px; font-weight: 500; margin-left: 1px; margin-bottom: 6px; }
  .field__input { width: 305px; height: 36px; border: 1px solid var(--border); background: var(--white); font-family: inherit; font-size: 12px; padding: 0 11px; color: var(--ink); }
  .field__input::placeholder { color: var(--placeholder); }
  .field__hint { display: block; font-size: 11px; color: var(--muted); margin: 7px 0 0 2px; }
  .submit { position: absolute; left: 184px; top: 399px; width: 122px; height: 40px; border: 1px solid var(--dark); border-radius: 20px; padding: 2px; }
  .submit__btn { width: 100%; height: 100%; border: none; border-radius: 18px; background: var(--dark); color: var(--white); font-family: inherit; font-size: 15px; font-weight: 500; }

  .hero-photo { position: absolute; left: 600px; top: 128px; width: 600px; height: 542px; background: linear-gradient(100deg, #45393f 0%, #5a4a4c 35%, #8a6d5f 60%, #4a4544 85%, #2f3a3a 100%); }
  .accent-bar { position: absolute; left: 592px; top: 286px; width: 17px; height: 384px; background: var(--red); }

  .footer { position: absolute; left: 0; top: 670px; width: 1200px; height: 40px; background: var(--dark); }
  .footer__copy { position: absolute; left: 87px; top: 11px; font-size: 13.5px; color: var(--white); }
  .footer__links { position: absolute; left: 520px; top: 11px; font-size: 13.5px; color: var(--footer-link); }
  .footer__links span { margin: 0 5px; }
  .social { position: absolute; left: 997px; top: 10px; display: flex; gap: 11px; }
  .social__item { width: 20px; height: 20px; border-radius: 50%; background: var(--white); }
</style>
</head>
<body>
  <header>
    <div class="topbar">
      <span class="topbar__info">Les renseignements CINQUANTE-HUIT utiles</span>
      <span class="topbar__lang">
        <svg width="20" height="20" viewBox="0 0 20 20" fill="none" stroke="#d21c22" stroke-width="1.3"><circle cx="10" cy="10" r="8.5"/><ellipse cx="10" cy="10" rx="3.8" ry="8.5"/><line x1="1.5" y1="10" x2="18.5" y2="10"/><line x1="3" y1="5.5" x2="17" y2="5.5"/><line x1="3" y1="14.5" x2="17" y2="14.5"/></svg>
        En
        <svg width="8" height="5" viewBox="0 0 8 5"><path d="M0 0h8L4 5z" fill="#333"/></svg>
      </span>
    </div>
    <nav class="navbar">
      <div class="brand"><span class="brand__dot"></span><span class="brand__name">5858</span></div>
      <div class="nav">
        <a class="nav__item nav__item--active">Individuals</a>
        <a class="nav__item">Companies</a>
        <a class="nav__item">Inversed annual</a>
        <a class="nav__item">International</a>
      </div>
      <div class="quote"><span class="quote__btn">Get a Quote</span></div>
    </nav>
  </header>

  <main>
    <form class="search">
      <div class="field" style="top:99px">
        <label class="field__label">Surname:</label>
        <input class="field__input" type="text" placeholder="Type here">
        <span class="field__hint">Ex: Dupont, Janssens, ...</span>
      </div>
      <div class="field" style="top:196px">
        <label class="field__label">First Name:</label>
        <input class="field__input" type="text" placeholder="Type here">
        <span class="field__hint">Eg: Jan, Louis, ...</span>
      </div>
      <div class="field" style="top:293px">
        <label class="field__label">Locality:</label>
        <input class="field__input" type="text" placeholder="Type here">
        <span class="field__hint">Ex: Liège, Antwerp, 1150, ...</span>
      </div>
      <div class="submit"><button class="submit__btn" type="button">Submit</button></div>
    </form>
    <div class="hero-photo" role="img" aria-label="Photo of a young woman wearing headphones, looking to the side"></div>
    <div class="accent-bar"></div>
  </main>

  <footer class="footer">
    <span class="footer__copy">Copyright © 58 58. All Rights Reserved</span>
    <span class="footer__links">B2B ServicesHelp<span>|</span>Terms of Use<span>|</span>Privacy</span>
    <div class="social">
      <span class="social__item"></span>
      <span class="social__item"></span>
      <span class="social__item"></span>
      <span class="social__item"></span>
    </div>
  </footer>
</body>
</html>
```